Webdesign für Bedrucken Papiertaschen, Schildern etc.
Zielgruppe
Wir bedrucken Papiertaschen, Papierbeutel, Laternen, Aluplaketten, Schilder, etc. und lasern Hundemarken. Zielgruppen von Privat bis Geschäftskunden
Aufgabenstellung
Der Shop sollte ein einfacher und kostengünstiger 'web2print'-shop werden. Wo die Kunden anhand von einem Editor Ihre Logos oder Druckvorlagen selber hochladen und/oder gestalten könne. Bisher haben die Kunden eifach ihre Bidldatei per E-Mail geschickt und wir haben diese dann weiter verarbeit.
Der Shop sollte, wenn möglich, günstig im Unterhalt sein, da wir nicht abschätzen können, wie gut diese laufen wird.
Wir haben wie 3 Bereich: 1. Papierbeutel/Taschen / 2. Stallplaketten (für z.B. Pferdesport) / 3. Diverses (Wie z.B. die Laternen, Schilder, Hundemarken, etc.)
Es würde sich um eine separate Webseite handeln. Daher ist bei Design freie Hand, eifach und klar... auch für nicht so ambitionierte Privatkunden oder kleine Unternehmen.

```html
<!DOCTYPE html>
<html lang="de">
<head>
<meta charset="utf-8">
<title>Tütenwerk – Gestalten</title>
<link href="https://fonts.googleapis.com/css2?family=Inter:wght@400;500;600;700;800&family=IBM+Plex+Mono:wght@400;500&display=swap" rel="stylesheet">
<style>
:root{
  --red:#d9261c;
  --red-soft:#f7d9d6;
  --ink:#111;
  --muted:#6b6b6b;
  --line:#e3e3e3;
  --paper:#fff;
  --stage:#f1f1ee;
  --kraft:#c4a574;
  --kraft-dark:#b89764;
  --black:#0c0c0c;
}
*{box-sizing:border-box;margin:0;padding:0}
html,body{width:1200px;height:750px;overflow:hidden}
body{position:relative;background:var(--paper);font-family:Inter,sans-serif;color:var(--ink)}
.mono{font-family:"IBM Plex Mono",monospace}
.abs{position:absolute}

/* top info bar */
.infobar{left:0;top:0;width:1200px;height:24px;background:var(--black);color:#fff;font-family:"IBM Plex Mono",monospace;font-size:9.5px;letter-spacing:.04em;display:flex;align-items:center;justify-content:space-between;padding:0 19px 0 46px}
.infobar .dot{position:absolute;left:47px;top:10px;width:4px;height:4px;border-radius:50%;background:var(--red)}
.infobar .first{padding-left:10px}

/* header */
.header{left:0;top:24px;width:1200px;height:63px;border-bottom:1px solid var(--line)}
.back{left:20px;top:22px}
.brand{left:47px;top:12px;width:48px;height:38px;display:flex;align-items:center;justify-content:center;font-weight:800;font-size:13px;letter-spacing:-.03em}
.brand-sep{left:106px;top:14px;width:1px;height:34px;background:var(--line)}
.product{left:122px;top:12px}
.product h1{font-size:11px;font-weight:600}
.product p{font-size:9px;color:var(--muted);line-height:13px;margin-top:3px;width:215px}
.step{top:20px;height:22px;border-radius:11px;font-family:"IBM Plex Mono",monospace;font-size:9.5px;letter-spacing:.05em;display:flex;align-items:center;justify-content:center;gap:4px;color:#555}
.step.done{left:396px;width:76px;background:var(--red-soft);color:var(--red)}
.step.now{left:493px;width:91px;background:var(--red);color:#fff}
.step.s3{left:614px}
.step.s4{left:720px}
.dash{top:31px;width:11px;height:1px;background:#ccc}
.autosave{left:817px;top:19px;font-size:9.5px;color:var(--muted);line-height:12px}
.btn-outline{left:933px;top:15px;width:99px;height:33px;border:1px solid var(--ink);border-radius:17px;display:flex;align-items:center;justify-content:center;gap:8px;font-size:11px;font-weight:600}
.btn-red{left:1040px;top:15px;width:140px;height:33px;background:var(--red);color:#fff;border-radius:17px;display:flex;align-items:center;justify-content:center;gap:8px;font-size:11px;font-weight:600}

/* left rail */
.rail{left:0;top:87px;width:59px;height:663px;background:var(--black)}
.rail-item{position:absolute;left:0;width:59px;height:50px;display:flex;flex-direction:column;align-items:center;justify-content:center;gap:5px;color:#bbb;font-family:"IBM Plex Mono",monospace;font-size:7.5px;letter-spacing:.08em}
.rail-item.active{background:#262626;color:#fff;box-shadow:inset 2px 0 0 var(--red)}

/* left panel */
.left{left:59px;top:87px;width:267px;height:663px;border-right:1px solid var(--line)}
.left h2{position:absolute;left:19px;top:21px;font-size:15px;font-weight:600;letter-spacing:-.01em}
.left .sub{position:absolute;left:19px;top:43px;font-size:9.5px;color:var(--muted)}
.drop{left:19px;top:74px;width:229px;height:181px;border:1.5px dashed #ddd;border-radius:6px;text-align:center}
.drop .icon{position:absolute;left:94px;top:27px;width:40px;height:40px;border-radius:50%;background:var(--red-soft);display:flex;align-items:center;justify-content:center}
.drop .t1{position:absolute;left:0;width:100%;top:80px;font-size:11px;font-weight:600}
.drop .t2{position:absolute;left:0;width:100%;top:98px;font-size:9.5px;color:var(--muted)}
.drop .pick{position:absolute;left:66px;top:119px;width:96px;height:32px;border-radius:16px;background:var(--red);color:#fff;font-size:11px;font-weight:600;display:flex;align-items:center;justify-content:center}
.label{font-family:"IBM Plex Mono",monospace;font-size:9.5px;letter-spacing:.1em;color:#555}
.file{left:19px;width:229px;border:1px solid var(--line);border-radius:5px}
.file .badge{position:absolute;left:11px;width:33px;height:33px;border-radius:4px;display:flex;align-items:center;justify-content:center;font-family:"IBM Plex Mono",monospace;font-size:8px;font-weight:500}
.file .name{position:absolute;left:53px;font-size:11px;font-weight:600}
.file .meta{position:absolute;left:53px;font-size:8.5px;color:var(--muted);line-height:12px;width:120px}
.check{position:absolute;left:194px;top:17px;width:23px;height:23px;border:1.5px solid var(--ink);border-radius:2px;display:flex;align-items:center;justify-content:center}
.tips{left:19px;top:436px;width:229px;height:102px;border:1px solid #f0c4bf;border-radius:6px}
.tips h3{position:absolute;left:37px;top:13px;font-size:11px;font-weight:600}
.tips p{position:absolute;left:37px;top:34px;width:185px;font-size:9.5px;line-height:15px;color:#333}

/* stage */
.toolbar{left:326px;top:87px;width:624px;height:44px;border-bottom:1px solid var(--line);display:flex;align-items:center;padding-left:21px;font-size:9.5px;color:#444}
.toolbar .g{color:var(--muted);letter-spacing:.05em}
.tool{position:absolute;top:11px;width:23px;height:23px;border:1px solid #ddd;border-radius:4px;display:flex;align-items:center;justify-content:center}
.zoom{position:absolute;left:546px;top:16px;font-size:10px;color:#333}
.stage{left:326px;top:131px;width:624px;height:619px;background:var(--stage);border-right:1px solid var(--line)}
.bag{position:absolute;left:137px;top:85px;width:350px;height:450px;background:var(--kraft);border-radius:3px;box-shadow:0 18px 40px rgba(0,0,0,.12)}
.bag .flap{position:absolute;left:0;top:0;width:100%;height:13px;background:var(--kraft-dark);border-radius:3px 3px 0 0}
.bag .fold{position:absolute;top:13px;bottom:0;width:1px;background:rgba(0,0,0,.08)}
.bag .safe{position:absolute;left:12px;top:13px;right:12px;bottom:12px;border:1px dashed rgba(217,38,28,.55)}
.bag .safe-label{position:absolute;left:15px;top:17px;font-size:7px;color:var(--red);opacity:.6;letter-spacing:.06em}
.sel{position:absolute;left:91px;top:134px;width:167px;height:81px;border:1px solid #111}
.h{position:absolute;width:6px;height:6px;background:#fff;border:1px solid #111}
.rot{position:absolute;left:77px;top:-17px;width:12px;height:12px;border-radius:50%;background:#fff;border:1px solid #111;font-size:8px;display:flex;align-items:center;justify-content:center}
.logo-word{position:absolute;left:0;width:100%;top:17px;text-align:center;color:var(--red);font-weight:700;font-size:22px;letter-spacing:-.02em}
.logo-rule{position:absolute;left:55px;top:47px;width:57px;height:1.5px;background:var(--red)}
.logo-sub{position:absolute;left:0;width:100%;top:54px;text-align:center;color:var(--red);font-size:7.5px;letter-spacing:.12em}
.dims{position:absolute;left:110px;top:223px;width:131px;height:16px;background:#111;color:#fff;border-radius:2px;font-size:8px;display:flex;align-items:center;justify-content:center}
.url{position:absolute;left:0;width:100%;top:393px;text-align:center;color:var(--red);font-size:8.5px;letter-spacing:.08em}
.tabs{position:absolute;left:184px;top:563px;width:258px;height:35px;background:#fff;border-radius:18px;box-shadow:0 4px 14px rgba(0,0,0,.08);display:flex;align-items:center;padding:0 4px;font-size:11px;font-weight:600}
.tabs span{height:27px;display:flex;align-items:center;justify-content:center;border-radius:14px}
.tabs .on{background:var(--red);color:#fff;width:85px}

/* right panel */
.right{left:950px;top:87px;width:250px;height:663px}
.right .label{position:absolute;left:19px}
.right .title{position:absolute;left:19px;top:36px;font-size:15px;font-weight:600}
.field{position:absolute;width:103px;height:41px;border:1px solid var(--line);border-radius:4px}
.field small{position:absolute;left:9px;top:8px;font-family:"IBM Plex Mono",monospace;font-size:7px;color:var(--muted)}
.field b{position:absolute;left:9px;top:21px;font-family:"IBM Plex Mono",monospace;font-size:11px;font-weight:400}
.align{position:absolute;top:220px;width:32px;height:30px;border:1px solid var(--line);border-radius:4px;display:flex;align-items:center;justify-content:center}
.color{position:absolute;left:19px;top:342px;width:213px;height:44px;border:1px solid var(--line);border-radius:5px}
.color .sw{position:absolute;left:10px;top:13px;width:18px;height:18px;border-radius:50%;background:var(--red)}
.color b{position:absolute;left:35px;top:9px;font-size:11px;font-weight:600}
.color small{position:absolute;left:35px;top:26px;font-family:"IBM Plex Mono",monospace;font-size:8px;color:var(--muted)}
.fx{position:absolute;width:104px;height:28px;border:1px solid var(--line);border-radius:3px;display:flex;align-items:center;justify-content:center;font-size:10.5px;font-weight:500}
.fx.on{background:var(--red);border-color:var(--red);color:#fff}
.price{position:absolute;left:19px;top:550px;width:213px;height:95px;border:1px solid var(--line);border-radius:6px}
.price .lbl{position:absolute;left:12px;top:26px;font-size:9px;line-height:12px;letter-spacing:.1em;color:#555}
.price .amt{position:absolute;left:100px;top:15px;font-size:21px;font-weight:700;letter-spacing:-.03em}
.price .bar{position:absolute;left:100px;top:55px;width:20px;height:2px;background:var(--ink)}
.price .calc{position:absolute;left:12px;top:72px;font-size:8.5px;color:#444}
</style>
</head>
<body>

<div class="abs infobar">
  <i class="dot"></i>
  <span class="first">VERSAND CH AB CHF 9.50 — DE/FR/IT VERFÜGBAR</span>
  <span>DRUCK IN 3–5 WERKTAGEN · LASERGRAVUR AB 24 H</span>
  <span>HILFE? +41 44 000 12 34</span>
</div>

<header class="abs header">
  <svg class="abs back" width="10" height="14" viewBox="0 0 10 14"><path d="M3 3l4 4-4 4" fill="none" stroke="#d9261c" stroke-width="1.5"/></svg>
  <div class="abs brand">Tütenwerk</div>
  <div class="abs brand-sep"></div>
  <div class="abs product">
    <h1>Faltenbeutel braun · M (16×26 cm)</h1>
    <p class="mono">500 Stk. · 1-farbig Pantone 7621 C · Entwurf #A-7126</p>
  </div>
  <div class="abs step done"><svg width="9" height="9" viewBox="0 0 10 10"><path d="M2 5l2 2 4-4" fill="none" stroke="#d9261c" stroke-width="1.4"/></svg>PRODUKT</div>
  <div class="abs dash" style="left:478px"></div>
  <div class="abs step now">02 GESTALTEN</div>
  <div class="abs dash" style="left:590px"></div>
  <div class="abs step s3">03 VORSCHAU</div>
  <div class="abs dash" style="left:696px"></div>
  <div class="abs step s4">04 BESTELLEN</div>
  <div class="abs autosave mono">Auto-Speichern ·<br>11:42</div>
  <div class="abs btn-outline"><svg width="13" height="9" viewBox="0 0 14 10"><path d="M1 5c2-3 4-4 6-4s4 1 6 4c-2 3-4 4-6 4S3 8 1 5z" fill="none" stroke="#111" stroke-width="1.2"/><circle cx="7" cy="5" r="1.7" fill="none" stroke="#111" stroke-width="1.2"/></svg>Vorschau</div>
  <div class="abs btn-red">In den Warenkorb <svg width="11" height="9" viewBox="0 0 12 10"><path d="M1 5h9M7 2l3 3-3 3" fill="none" stroke="#fff" stroke-width="1.3"/></svg></div>
</header>

<nav class="abs rail">
  <div class="rail-item active" style="top:14px"><svg width="14" height="14" viewBox="0 0 14 14"><path d="M7 10V2M4 5l3-3 3 3M2 12h10" fill="none" stroke="#fff" stroke-width="1.3"/></svg>UPLOAD</div>
  <div class="rail-item" style="top:67px"><svg width="14" height="14" viewBox="0 0 14 14"><path d="M3 3h8M7 3v9M5 12h4" fill="none" stroke="#ddd" stroke-width="1.3"/></svg>TEXT</div>
  <div class="rail-item" style="top:120px"><svg width="14" height="14" viewBox="0 0 14 14"><rect x="1.5" y="2" width="11" height="10" rx="1.5" fill="none" stroke="#ddd" stroke-width="1.2"/><circle cx="5" cy="5.5" r="1.2" fill="#ddd"/><path d="M2 11l4-3 3 2 3-2" fill="none" stroke="#ddd" stroke-width="1.2"/></svg>LOGOS</div>
  <div class="rail-item" style="top:173px"><svg width="14" height="14" viewBox="0 0 14 14"><path d="M7 2l6 3-6 3-6-3zM1 8l6 3 6-3" fill="none" stroke="#ddd" stroke-width="1.2"/></svg>LAYER</div>
  <div class="rail-item" style="top:226px"><svg width="14" height="14" viewBox="0 0 14 14"><path d="M7 1l5 2v4c0 3-2 5-5 6-3-1-5-3-5-6V3z" fill="none" stroke="#ddd" stroke-width="1.2"/><path d="M4.5 7l2 2 3-3.5" fill="none" stroke="#ddd" stroke-width="1.2"/></svg>PRÜFEN</div>
</nav>

<aside class="abs left">
  <h2>Druckvorlage hochladen</h2>
  <p class="sub">PDF, SVG, EPS, AI oder PNG · max. 50 MB</p>
  <div class="abs drop">
    <div class="icon"><svg width="14" height="14" viewBox="0 0 14 14"><path d="M7 10V3M4 6l3-3 3 3M3 12h8" fill="none" stroke="#d9261c" stroke-width="1.3"/></svg></div>
    <p class="t1">Datei hierher ziehen</p>
    <p class="t2">oder klicken zum auswählen</p>
    <div class="pick">Datei wählen</div>
  </div>
  <p class="abs label" style="left:19px;top:275px">BEREITS HOCHGELADEN</p>
  <div class="abs file" style="top:294px;height:59px">
    <div class="badge" style="top:13px;background:var(--red-soft);color:var(--red)">PDF</div>
    <p class="name" style="top:12px">logo-vector.pdf</p>
    <p class="meta mono" style="top:30px">2.4 MB · Vektor · 300 dpi · CMYK</p>
    <div class="check"><svg width="10" height="10" viewBox="0 0 10 10"><path d="M2 5l2 2 4-4" fill="none" stroke="#111" stroke-width="1.3"/></svg></div>
  </div>
  <div class="abs file" style="top:362px;height:55px">
    <div class="badge" style="top:10px;background:#f1f1f1;color:#777">JPG</div>
    <p class="name" style="top:17px">foto-stall.jpg</p>
    <p class="meta mono" style="top:34px">1.1 MB · 72 dpi</p>
  </div>
  <div class="abs tips">
    <svg class="abs" style="left:13px;top:14px" width="14" height="14" viewBox="0 0 14 14"><path d="M7 1l5 2v4c0 3-2 5-5 6-3-1-5-3-5-6V3z" fill="none" stroke="#d9261c" stroke-width="1.2"/><path d="M4.5 7l2 2 3-3.5" fill="none" stroke="#d9261c" stroke-width="1.2"/></svg>
    <h3>Drucktipps</h3>
    <p>Für beste Qualität: Vektordaten (PDF/SVG), mind. 300 dpi, CMYK-Farbraum, Schriften eingebettet oder in Pfade umgewandelt.</p>
  </div>
</aside>

<div class="abs toolbar mono">
  <span class="g">2D DRUCKBOGEN</span>&nbsp;&nbsp;·&nbsp;&nbsp;<span style="font-family:Inter,sans-serif">Vorderseite</span>&nbsp;&nbsp;·&nbsp;&nbsp;160 × 260 mm + 3 mm Beschnitt
  <div class="tool" style="left:441px"><svg width="11" height="11" viewBox="0 0 11 11"><g fill="none" stroke="#333"><rect x="1" y="1" width="3.5" height="3.5"/><rect x="6.5" y="1" width="3.5" height="3.5"/><rect x="1" y="6.5" width="3.5" height="3.5"/><rect x="6.5" y="6.5" width="3.5" height="3.5"/></g></svg></div>
  <div class="tool" style="left:469px"><svg width="12" height="8" viewBox="0 0 14 10"><path d="M1 5c2-3 4-4 6-4s4 1 6 4c-2 3-4 4-6 4S3 8 1 5z" fill="none" stroke="#333" stroke-width="1.2"/><circle cx="7" cy="5" r="1.6" fill="none" stroke="#333" stroke-width="1.2"/></svg></div>
  <div class="tool" style="left:505px"><svg width="9" height="9" viewBox="0 0 9 9"><path d="M1 4.5h7" stroke="#333" stroke-width="1.2"/></svg></div>
  <span class="zoom">78%</span>
  <div class="tool" style="left:589px"><svg width="9" height="9" viewBox="0 0 9 9"><path d="M1 4.5h7M4.5 1v7" stroke="#333" stroke-width="1.2"/></svg></div>
</div>

<main class="abs stage">
  <div class="bag">
    <div class="flap"></div>
    <div class="fold" style="left:98px"></div>
    <div class="fold" style="left:252px"></div>
    <div class="safe"></div>
    <span class="safe-label mono">SICHERHEITSRAND 5 MM</span>
    <div class="sel">
      <div class="rot">↻</div>
      <i class="h" style="left:-4px;top:-4px"></i><i class="h" style="left:80px;top:-4px"></i><i class="h" style="right:-4px;top:-4px"></i>
      <i class="h" style="left:-4px;top:37px"></i><i class="h" style="right:-4px;top:37px"></i>
      <i class="h" style="left:-4px;bottom:-4px"></i><i class="h" style="left:80px;bottom:-4px"></i><i class="h" style="right:-4px;bottom:-4px"></i>
      <div class="logo-word">Logo</div>
      <div class="logo-rule"></div>
      <div class="logo-sub mono">Lorem Ipsum</div>
    </div>
    <div class="dims mono">80 × 28 mm · x:40 y:78</div>
    <div class="url mono">WWW.MUSTERDRUCK.CH</div>
  </div>
  <div class="tabs">
    <span class="on">Vorderseite</span>
    <span style="width:80px">Rückseite</span>
    <span style="width:85px">3D Vorschau</span>
  </div>
</main>

<aside class="abs right">
  <p class="label" style="top:20px">AUSWAHL</p>
  <p class="title">Logo · Lorem Ipsum</p>
  <p class="label" style="top:80px">POSITION</p>
  <div class="field" style="left:19px;top:92px"><small>X</small><b>40 mm</b></div>
  <div class="field" style="left:129px;top:92px"><small>Y</small><b>78 mm</b></div>
  <div class="field" style="left:19px;top:140px"><small>B</small><b>80 mm</b></div>
  <div class="field" style="left:129px;top:140px"><small>H</small><b>28 mm</b></div>
  <p class="label" style="top:207px">AUSRICHTUNG</p>
  <div class="align" style="left:19px"><svg width="10" height="10" viewBox="0 0 10 10"><path d="M9 5H1M4 2L1 5l3 3" fill="none" stroke="#111" stroke-width="1.1"/></svg></div>
  <div class="align" style="left:55px"><svg width="12" height="10" viewBox="0 0 12 10"><path d="M1 5h10M3.5 2.5L1 5l2.5 2.5M8.5 2.5L11 5 8.5 7.5" fill="none" stroke="#111" stroke-width="1.1"/></svg></div>
  <div class="align" style="left:90px"><svg width="10" height="10" viewBox="0 0 10 10"><path d="M1 5h8M6 2l3 3-3 3" fill="none" stroke="#111" stroke-width="1.1"/></svg></div>
  <div class="align" style="left:127px"><svg width="10" height="10" viewBox="0 0 10 10"><path d="M5 9V1M2 4l3-3 3 3" fill="none" stroke="#111" stroke-width="1.1"/></svg></div>
  <div class="align" style="left:163px"><svg width="10" height="12" viewBox="0 0 10 12"><path d="M5 1v10M2.5 3.5L5 1l2.5 2.5M2.5 8.5L5 11l2.5-2.5" fill="none" stroke="#111" stroke-width="1.1"/></svg></div>
  <div class="align" style="left:199px"><svg width="10" height="10" viewBox="0 0 10 10"><path d="M5 1v8M2 6l3 3 3-3" fill="none" stroke="#111" stroke-width="1.1"/></svg></div>
  <p class="label" style="top:275px">DREHUNG</p>
  <p class="abs mono" style="left:201px;top:290px;font-size:10.5px">0°</p>
  <p class="label" style="top:330px">DRUCKFARBE</p>
  <div class="color"><i class="sw"></i><b>Pantone 7621 C</b><small>rot-orange · 1-farbig</small></div>
  <p class="label" style="top:411px">EFFEKT</p>
  <div class="fx on" style="left:19px;top:424px">Kein</div>
  <div class="fx" style="left:128px;top:424px">Schatten</div>
  <div class="fx" style="left:19px;top:458px">Outline</div>
  <div class="fx" style="left:128px;top:458px">Glow</div>
  <div class="price">
    <p class="lbl mono">AKTUELLER<br>PREIS</p>
    <p class="amt">CHF 182.</p>
    <i class="bar"></i>
    <p class="calc mono">500 Stk. × 0.34 + 12.– Versand</p>
  </div>
</aside>

</body>
</html>
```